New Business Card Design Project

We are a spa looking to create a professional elegant business card for a spa mainly black and white with a splash of lime green. This card will be two sided - the front side will have an image, the logo, and the spa's information - the back side will have a promotion for new customers - NEW CUSTOMERS $20 OFF

Look and feel: chic, modern, and spa-ish.
Information to be included:
Therapist Name
Therapist specialty
Address: 4719 Marlowe Ave, Beverly Hills CA 90211
Phone: (310) 482-3917

Let me know if you have any questions!

Thank you

```html
<!DOCTYPE html>
<html lang="en">
<head>
<meta charset="utf-8">
<title>Lumen Day Spa – Business Card</title>
<link rel="stylesheet" href="https://fonts.googleapis.com/css2?family=Arimo:wght@400;700&display=swap">
<style>
  :root {
    --ink: #111111;
    --paper: #ffffff;
    --lime: #8cc63f;
    --lime-bright: #9ee02f;
    --stage: #ecebe8;
    --photo-light: #f6f1ea;
    --photo-warm: #e8cdb4;
  }
  * { box-sizing: border-box; margin: 0; padding: 0; }
  html, body {
    width: 1200px; height: 784px; overflow: hidden;
    background: var(--stage);
    font-family: "Arimo", Arial, sans-serif;
  }
  .canvas {
    width: 1200px; height: 784px;
    display: flex; align-items: center; justify-content: center; gap: 40px;
  }
  .card {
    width: 540px; height: 309px; position: relative; overflow: hidden;
    box-shadow: 0 6px 18px rgba(0,0,0,.18);
  }

  /* Back side */
  .card--back { background: var(--ink); }
  .back__ring {
    position: absolute; left: 50%; top: 50%;
    width: 230px; height: 230px; margin: -115px 0 0 -115px;
    border: 6px solid rgba(255,255,255,.05); border-radius: 50%;
  }
  .back__offer {
    position: absolute; left: 0; right: 0; top: 50%; transform: translateY(-50%);
    text-align: center; color: var(--lime-bright);
    font-weight: 700; font-size: 21px; letter-spacing: 6px;
  }

  /* Front side */
  .card--front { background: var(--paper); }
  .front__therapist {
    position: absolute; right: 22px; top: 16px; text-align: left;
  }
  .therapist__name { color: var(--lime); font-weight: 700; font-size: 15px; }
  .therapist__specialty { color: var(--ink); font-size: 12px; margin-top: 2px; }
  .front__photo {
    position: absolute; right: 0; top: 52px; width: 270px; height: 178px;
    background: radial-gradient(ellipse at 60% 45%, var(--photo-warm) 0%, var(--photo-light) 60%, var(--paper) 100%);
  }
  .front__brand {
    position: absolute; left: 44px; top: 70px;
    display: flex; align-items: center; gap: 12px;
  }
  .brand__mark {
    width: 30px; height: 30px; border-radius: 50%; background: var(--ink);
  }
  .brand__name {
    color: var(--ink); font-weight: 700; font-size: 26px;
  }
  .front__contact {
    position: absolute; left: 40px; top: 178px;
    color: var(--ink); font-size: 17px; line-height: 1.25;
  }
  .contact__row { display: flex; align-items: center; gap: 6px; }
  .contact__row svg { width: 15px; height: 15px; fill: var(--lime); flex: none; }
  .contact__indent { padding-left: 21px; }
  .front__band {
    position: absolute; left: 0; right: 0; bottom: 10px; height: 36px;
    background: var(--ink);
    border-top: 3px solid var(--lime);
  }
  .front__rule {
    position: absolute; left: 0; right: 0; bottom: 4px; height: 2px; background: var(--lime);
  }
</style>
</head>
<body>
<main class="canvas">
  <section class="card card--back" aria-label="Card back">
    <div class="back__ring"></div>
    <p class="back__offer">NEW CUSTOMERS $20 OFF</p>
  </section>

  <section class="card card--front" aria-label="Card front">
    <div class="front__photo" role="img" aria-label="Photo of a relaxing spa massage with candles"></div>
    <div class="front__therapist">
      <p class="therapist__name">Therapist Name</p>
      <p class="therapist__specialty">Therapist specialty</p>
    </div>
    <div class="front__brand">
      <span class="brand__mark"></span>
      <span class="brand__name">Lumen Day Spa</span>
    </div>
    <div class="front__contact">
      <p class="contact__row">
        <svg viewBox="0 0 24 24" aria-hidden="true"><path d="M6.6 10.8a15.1 15.1 0 0 0 6.6 6.6l2.2-2.2a1 1 0 0 1 1-.25 11.4 11.4 0 0 0 3.6.57 1 1 0 0 1 1 1V20a1 1 0 0 1-1 1A17 17 0 0 1 3 4a1 1 0 0 1 1-1h3.5a1 1 0 0 1 1 1c0 1.25.2 2.45.57 3.6a1 1 0 0 1-.25 1z"/></svg>
        (310) 482-3917
      </p>
      <p class="contact__row">
        <svg viewBox="0 0 24 24" aria-hidden="true"><path d="M12 3 2 12h3v8h5v-6h4v6h5v-8h3z"/></svg>
        4719 Marlowe Ave,
      </p>
      <p class="contact__indent">Beverly Hills CA 90211</p>
    </div>
    <div class="front__band"></div>
    <div class="front__rule"></div>
  </section>
</main>
</body>
</html>
```